Volbrey Inc Business Card

Looking to get an updated business card for a Contract Machining company (www.volbreyinc.example) - looking for a clean design the portrays the technical nature of the business - colors can follow the website design and be in any combination that makes sense (red black, white, metallic or silver) - logos attached for use also. Would like space for: Name, title, business phone (555 214-3086), cell phone , website (www.volbreyinc.example) - possibly QR code could be integrated for website (designer choice), business address - 418 Harlow Bend, Larkfield, OR 97199 (cards will be for 4 employees, I will either need to modify a template or I can provide individual information)
Target Market(s)
Aerospace, defense and medical device manufacturing companies that need machining
Industry/Entity Type
Machining for aerospace, defense, medical
Contact Information for Business Card
Name, Title, Business Phone, Cell Phone, email, business website and business address
Look and feel

```html
<!DOCTYPE html>
<html lang="en">
<head>
<meta charset="utf-8">
<title>Volbrey Inc Business Card</title>
<link href="https://fonts.googleapis.com/css2?family=Montserrat:wght@700;800&family=Roboto:wght@400;500&display=swap" rel="stylesheet">
<style>
  :root {
    --stage: #3b3b3b;
    --card-white: #ffffff;
    --card-black: #262626;
    --pattern-dark: #2f2f2f;
    --pattern-light: #3a3a3a;
    --brand-red: #b01e24;
    --ink: #3a3a3a;
    --ink-soft: #777777;
    --rule: #d8d8d8;
  }
  * { box-sizing: border-box; margin: 0; padding: 0; }
  html, body { width: 1200px; height: 803px; overflow: hidden; }
  body {
    background: var(--stage);
    display: flex;
    align-items: center;
    justify-content: center;
    gap: 48px;
    font-family: "Roboto", Arial, sans-serif;
  }
  .card {
    width: 525px;
    height: 300px;
    border-radius: 22px;
    border-bottom: 4px solid var(--brand-red);
    position: relative;
    overflow: hidden;
    box-shadow: 0 18px 40px rgba(0,0,0,.45);
  }
  .card--front { background: var(--card-white); display: flex; }
  .card--back { background: var(--card-black); }

  .front-brand {
    width: 48%;
    display: flex;
    flex-direction: column;
    align-items: center;
    justify-content: center;
    gap: 14px;
    padding: 0 16px;
  }
  .brand-dot {
    width: 112px; height: 112px;
    border-radius: 50%;
    background: var(--brand-red);
    flex: none;
  }
  .brand-name {
    font-family: "Montserrat", Arial, sans-serif;
    font-weight: 800;
    font-size: 24px;
    letter-spacing: 1px;
    color: var(--brand-red);
    text-transform: uppercase;
    white-space: nowrap;
  }
  .front-divider {
    width: 1px;
    margin: 40px 0;
    background: linear-gradient(var(--card-white), var(--rule), var(--card-white));
  }
  .front-info {
    flex: 1;
    padding: 48px 20px 40px 30px;
    display: flex;
    flex-direction: column;
    gap: 16px;
  }
  .person-name {
    font-family: "Montserrat", Arial, sans-serif;
    font-weight: 700;
    font-size: 22px;
    color: var(--brand-red);
  }
  .person-title { font-size: 12px; color: var(--ink-soft); margin-top: 2px; }
  .address, .contacts { font-size: 13px; color: var(--ink); line-height: 1.45; }
  .contacts { list-style: none; }
  .contacts li { display: flex; align-items: center; gap: 8px; white-space: nowrap; }
  .contacts svg { width: 11px; height: 11px; flex: none; fill: var(--brand-red); }

  .back-pattern {
    position: absolute; inset: 0;
    background: radial-gradient(circle at 70% 20%, var(--pattern-light), var(--pattern-dark) 55%, var(--card-black));
  }
  .back-brand {
    position: absolute;
    right: 40px; bottom: 56px;
    display: flex; align-items: center; gap: 14px;
  }
  .back-brand .brand-dot { width: 62px; height: 62px; }
  .back-brand .brand-name { font-size: 26px; }
</style>
</head>
<body>
  <section class="card card--front">
    <div class="front-brand">
      <span class="brand-dot"></span>
      <span class="brand-name">Volbrey Inc.</span>
    </div>
    <div class="front-divider"></div>
    <div class="front-info">
      <div>
        <p class="person-name">Dale Werner</p>
        <p class="person-title">President</p>
      </div>
      <p class="address">418 Harlow Bend<br>Larkfield, OR 97199</p>
      <ul class="contacts">
        <li><svg viewBox="0 0 10 10"><path d="M2 0h2l1 3-1.5 1a6 6 0 0 0 2.5 2.5L7 5l3 1v2c0 1-1 2-2 2A8 8 0 0 1 0 2c0-1 1-2 2-2z"/></svg>555 214-3086</li>
        <li><svg viewBox="0 0 10 10"><path d="M2 0h6v10H2zM3 1v7h4V1z"/></svg>555 308-7721</li>
        <li><svg viewBox="0 0 10 10"><path d="M0 2h10v6H0zM1 3l4 3 4-3z"/></svg>info@volbreyinc.example</li>
        <li><svg viewBox="0 0 10 10"><circle cx="5" cy="5" r="5"/></svg>www.volbreyinc.example</li>
      </ul>
    </div>
  </section>

  <section class="card card--back">
    <div class="back-pattern" role="img" aria-label="Embossed repeating brand pattern in dark grey tones"></div>
    <div class="back-brand">
      <span class="brand-dot"></span>
      <span class="brand-name">Volbrey Inc.</span>
    </div>
  </section>
</body>
</html>
```